Business card for my new company (Accounting firm)

I need a business card for my new business Brightwell Advisory and Ledger SA. Our services are accounting, tax, audit and financial management. Our customers are small companies, start-ups and new companies. The final design has to show financial security, trust and growth. Please find our logo attached to the business card. Text for the business card: Brightwell Advisory and Ledger SA Tomas Varenholt Director and Founder Certified Accountant Tel. 022 418 57 34 tv@clairevalconseil.ch www.clairevalconseil.ch Rue des Vergières 27 1201 Geneva
Target Market(s)
Our customers are small companies, start-ups and new companies.
Industry/Entity Type
Finance And Accounting
Contact Information for Business Card
Claireval Conseil et Comptes SA
Tomas Varenholt
Directeur et Fondateur
Expert-comptable diplômé
Tél. 022 418 57 34
tv@clairevalconseil.ch
www.clairevalconseil.ch
Rue des Vergières 27
1201 Genève

```html
<!DOCTYPE html>
<html lang="fr">
<head>
<meta charset="utf-8">
<title>Claireval Conseil et Comptes – Carte de visite</title>
<link rel="stylesheet" href="https://fonts.googleapis.com/css2?family=Roboto:wght@400;500;700&family=Montserrat:wght@400;500;600&display=swap">
<style>
  :root {
    --backdrop: #2a2828;
    --paper: #ffffff;
    --sky: #31aee0;
    --ink: #3b3b3d;
    --rule: #8c8c8c;
  }
  * { box-sizing: border-box; margin: 0; padding: 0; }
  html, body {
    width: 1125px;
    height: 1200px;
    overflow: hidden;
    background: var(--backdrop);
  }
  .stage { position: relative; width: 1125px; height: 1200px; }

  .card {
    position: absolute;
    left: 171px;
    width: 826px;
    height: 472px;
    overflow: hidden;
  }
  .card--front { top: 106px; background: var(--paper); }
  .card--back  { top: 659px; background: var(--sky); }

  /* front */
  .brand {
    position: absolute;
    left: 120px;
    top: 215px;
    width: 240px;
    text-align: center;
    font-family: "Montserrat", sans-serif;
    font-weight: 500;
    color: var(--ink);
  }
  .brand__mark {
    display: block;
    width: 34px;
    height: 34px;
    margin: 0 auto 14px;
    background: var(--sky);
  }
  .brand__name {
    font-size: 22px;
    line-height: 1.25;
    letter-spacing: 1px;
  }
  .divider {
    position: absolute;
    left: 376px;
    top: 127px;
    width: 2px;
    height: 213px;
    background: var(--rule);
  }
  .contact {
    position: absolute;
    left: 412px;
    top: 128px;
    font-family: "Roboto", sans-serif;
    color: var(--ink);
    font-size: 19.5px;
    line-height: 27px;
  }
  .contact__name {
    font-size: 29px;
    font-weight: 700;
    color: var(--sky);
    line-height: 34px;
    margin-bottom: 0;
  }
  .contact__block { margin-top: 12px; }
  .contact__block--roles { margin-top: 0; }
  .contact__block--lines { margin-top: 9px; }

  .web-band {
    position: absolute;
    left: 0;
    top: 400px;
    width: 100%;
    height: 37px;
    background: var(--sky);
    color: var(--paper);
    font-family: "Roboto", sans-serif;
    font-size: 19px;
    letter-spacing: 4.4px;
    line-height: 37px;
    text-align: center;
  }

  /* back */
  .back-brand {
    position: absolute;
    right: 82px;
    top: 300px;
    text-align: right;
    color: var(--paper);
  }
  .back-brand__name {
    font-family: "Montserrat", sans-serif;
    font-weight: 500;
    font-size: 48px;
    letter-spacing: 2px;
    line-height: 1.1;
  }
  .back-brand__sub {
    font-family: "Montserrat", sans-serif;
    font-weight: 500;
    font-size: 48px;
    letter-spacing: 2px;
    line-height: 1.1;
    display: none;
  }
  .back-brand__web {
    margin-top: 14px;
    font-family: "Roboto", sans-serif;
    font-size: 19px;
    letter-spacing: 2.6px;
  }
</style>
</head>
<body>
<main class="stage">

  <section class="card card--front" aria-label="Recto de la carte">
    <div class="brand">
      <span class="brand__mark" aria-hidden="true"></span>
      <p class="brand__name">CLAIREVAL<br>CONSEIL ET COMPTES</p>
    </div>

    <div class="divider" aria-hidden="true"></div>

    <div class="contact">
      <p class="contact__name">Tomas Varenholt</p>
      <p class="contact__block contact__block--roles">Directeur et Fondateur<br>Expert-comptable diplômé</p>
      <p class="contact__block">Rue des Vergières 27<br>1201 Genève</p>
      <p class="contact__block contact__block--lines">P: 022 418 57 34<br>E: tv@clairevalconseil.ch</p>
    </div>

    <div class="web-band">www.clairevalconseil.ch</div>
  </section>

  <section class="card card--back" aria-label="Verso de la carte">
    <div class="back-brand">
      <p class="back-brand__name">CLAIREVAL</p>
      <p class="back-brand__web">www.clairevalconseil.ch</p>
    </div>
  </section>

</main>
</body>
</html>
```